Start up Dialysis Clinic needs its first website - Velmira Health

Create a visually appealing and user-friendly website for Velmira Health, a dialysis clinic located in Mt. Irvine, Tobago. The website should effectively communicate our services to local, regional, and international patients, providing essential information and fostering trust and engagement..
Key Goals:

1. Informative: Provide comprehensive information about our services, facility, and team.
2. User-Friendly: Ensure the website is easy to navigate, with a clear structure and accessible content.
3. Engaging: Create a visually appealing design that reflects the professionalism and care of Velmira Health.
4. Responsive: Ensure the website is fully responsive and performs well on all devices, including desktops, tablets, and smartphones.
5. Trust-Building: Include testimonials, credentials, and patient resources to build trust with potential patients.
Scope of Work:

1. Home Page: An inviting and informative landing page that provides an overview of our clinic, mission, and services. Include a call to action for more information and contact details.
2. About Us: A detailed page about Velmira Health, including our mission, vision, team, and facility tour.
3. Services: A comprehensive page describing the dialysis services we offer, including Hemodialysis, Peritoneal Dialysis, and Home Hemodialysis.
4. Patient Information: A resourceful section with guides for new patients, FAQs, insurance and billing information, and downloadable forms.
5. Resources: Educational content about kidney health, dialysis options, diet and nutrition tips, and support groups.
6. Contact Us: A contact page with our address, phone number, email, office hours, a contact form, and a map.

```html
<!DOCTYPE html>
<html lang="en">
<head>
<meta charset="utf-8">
<title>Velmira Health — Dialysis Clinic</title>
<link rel="stylesheet" href="https://fonts.googleapis.com/css2?family=Montserrat:ital,wght@0,400;0,500;0,600;0,700;0,800;1,700&family=Open+Sans:wght@400;600&display=swap">
<style>
:root{
  --blue:#3d70c6;
  --blue-dark:#2c5aa8;
  --green:#5e9f3e;
  --green-dark:#4e8a33;
  --white:#ffffff;
  --ink:#222a35;
  --muted:#6b7280;
  --line:#e3e7ee;
  --star:#f2b01e;
}
*{box-sizing:border-box;margin:0;padding:0}
html,body{width:1200px;height:3576px;overflow:hidden}
body{font-family:"Open Sans",Arial,sans-serif;color:var(--ink);background:var(--white);position:relative}
h1,h2,h3,h4,.nav,.btn,.tab{font-family:"Montserrat",Arial,sans-serif}
.btn{display:inline-block;background:var(--white);color:var(--ink);font-weight:700;font-size:14px;padding:12px 24px;border-radius:3px;letter-spacing:.5px}
.brand{display:flex;align-items:center;gap:10px;color:var(--white);font-family:"Montserrat",Arial,sans-serif;font-weight:700;font-size:20px;letter-spacing:.5px}
.brand-mark{width:24px;height:24px;background:var(--white)}

/* hero */
.hero{position:absolute;left:0;top:0;width:1200px;height:600px}
.hero-photo{position:absolute;inset:0;background:linear-gradient(100deg,#2f5fae 0%,#6f93c9 38%,#c9d6e6 62%,#8ea6c7 100%)}
.hero-shade{position:absolute;inset:0;background:linear-gradient(90deg,rgba(40,80,160,.75) 0%,rgba(40,80,160,.15) 45%,rgba(0,0,0,0) 70%)}
.topbar{position:absolute;left:112px;right:112px;top:20px;display:flex;align-items:center}
.nav{display:flex;gap:34px;margin-left:150px;color:var(--white);font-size:15px;font-weight:500}
.topbar .btn{margin-left:auto}
.hero-copy{position:absolute;left:112px;top:208px;color:var(--white)}
.hero-copy h1{font-size:34px;font-weight:700;line-height:1.2;letter-spacing:.5px}
.hero-copy h1 span{display:block;font-size:46px}
.hero-copy p{margin-top:14px;font-size:16px;line-height:1.5;width:340px}
.hero-copy .btn{margin-top:38px}

/* info band */
.info{position:absolute;left:0;top:600px;width:1200px;height:272px;background:var(--green);display:flex;padding:0 90px}
.info-item{flex:1;text-align:center;color:var(--white);padding-top:70px}
.info-icon{width:44px;height:44px;border-radius:50%;background:var(--white);margin:0 auto 18px;display:flex;align-items:center;justify-content:center}
.info-item h4{font-size:18px;font-weight:700;margin-bottom:6px}
.info-item p{font-size:15px;line-height:1.45}

/* services */
.services{position:absolute;left:0;top:872px;width:1200px;height:616px}
.section-title{font-family:"Montserrat",Arial,sans-serif;font-weight:700;font-size:34px;color:var(--green);text-align:center}
.services .section-title{margin-top:76px}
.cards{position:absolute;left:108px;top:120px;display:flex;gap:20px}
.card{width:313px;height:428px;background:var(--white);box-shadow:0 4px 18px rgba(0,0,0,.12)}
.card-photo{height:208px}
.card h3{text-align:center;font-size:19px;font-weight:700;margin:30px 0 14px}
.card p{font-size:14px;line-height:1.55;color:var(--muted);text-align:center;padding:0 22px}
.card .more{display:block;text-align:center;margin-top:18px;color:var(--green);font-size:14px;font-weight:600}

/* about */
.about{position:absolute;left:0;top:1488px;width:1200px;height:612px;background:var(--blue)}
.about h2{color:var(--white);font-size:38px;font-weight:700;text-align:center;margin-top:56px}
.tabs{position:absolute;left:112px;top:136px;display:flex;gap:30px}
.tab{width:224px;height:56px;background:var(--white);color:var(--ink);font-weight:700;font-size:17px;display:flex;align-items:center;justify-content:center;border-radius:3px}
.tab.active{background:var(--green);color:var(--white)}
.vision{position:absolute;left:112px;top:230px;width:510px;color:var(--white)}
.vision h3{font-size:30px;font-weight:700}
.vision h4{font-size:24px;font-weight:700;margin-top:10px}
.vision p{font-size:16px;line-height:1.6;margin-top:14px}
.vision .btn{margin-top:40px}
.vision-photo{position:absolute;left:672px;top:224px;width:416px;height:320px;border-radius:4px;background:radial-gradient(circle at 50% 50%,#d45a3a 0%,#7a2f4a 35%,#1d3766 70%,#17294d 100%)}

/* reviews */
.reviews{position:absolute;left:0;top:2100px;width:1200px;height:468px}
.reviews .section-title{margin-top:72px}
.review-row{position:absolute;left:110px;top:148px;display:flex;gap:30px}
.review{width:306px;height:252px;background:var(--white);box-shadow:0 4px 18px rgba(0,0,0,.12);padding:26px 28px}
.review-head{display:flex;align-items:center;gap:14px}
.avatar{width:56px;height:56px;border-radius:50%;background:linear-gradient(135deg,#c08a6c,#5d3b2c)}
.review-head h4{font-size:18px;font-weight:600}
.review-head small{display:block;font-size:12px;color:var(--muted)}
.stars{color:var(--star);font-size:16px;letter-spacing:2px}
.review p{font-size:14px;line-height:1.55;color:var(--muted);margin-top:20px}
.arrow{position:absolute;top:240px;width:32px;height:32px;border-radius:50%;border:2px solid var(--green);display:flex;align-items:center;justify-content:center}
.arrow.left{left:28px}.arrow.right{right:28px}

/* contact */
.map{position:absolute;left:0;top:2568px;width:600px;height:472px;background:linear-gradient(135deg,#e8ece4 0%,#dde5ea 55%,#a8c9e6 100%)}
.contact{position:absolute;left:600px;top:2568px;width:600px;height:472px;background:var(--blue);padding:44px 40px}
.contact h2{color:var(--white);font-size:38px;font-weight:500;letter-spacing:1px}
.form{margin-top:34px;display:grid;grid-template-columns:1fr 1fr;gap:22px 30px;width:520px}
.field{height:46px;background:var(--white);border-radius:3px;font-size:13px;color:#8a93a0;padding:14px}
.field.wide{grid-column:1/3;height:112px}
.submit{margin-top:22px;display:inline-block;background:var(--green);color:var(--white);font-family:"Montserrat",Arial,sans-serif;font-weight:700;font-size:14px;padding:10px 30px;border-radius:22px}

/* footer */
.footer{position:absolute;left:0;top:3040px;width:1200px;height:536px;background:var(--green);color:var(--white)}
.footer .brand{position:absolute;left:0;right:0;top:44px;justify-content:center;font-size:26px}
.footer .brand-mark{width:30px;height:30px}
.cols{position:absolute;left:112px;top:196px;display:flex}
.col{width:218px}
.col h4{font-style:italic;font-weight:700;font-size:22px;margin-bottom:16px}
.col li{list-style:none;font-size:16px;line-height:1.75}
.contact-list li{display:flex;align-items:center;gap:14px;margin-bottom:10px}
.mini{width:30px;height:30px;border-radius:50%;background:var(--white);flex:none;display:flex;align-items:center;justify-content:center}
.social{display:flex;gap:8px;margin-top:4px}
.social span{width:26px;height:26px;border-radius:50%;background:var(--white)}
.copy{position:absolute;left:112px;right:112px;top:456px;border-top:1px solid rgba(255,255,255,.5);padding-top:16px;text-align:center;font-size:15px}
</style>
</head>
<body>

<header class="hero">
  <div class="hero-photo" role="img" aria-label="Nurse adjusting a dialysis machine beside a seated patient"></div>
  <div class="hero-shade"></div>
  <div class="topbar">
    <div class="brand"><span class="brand-mark"></span>Velmira Health</div>
    <nav class="nav"><span>Home</span><span>About Us ▾</span><span>Our Services ▾</span><span>Patient Information ▾</span><span>Resources</span></nav>
    <span class="btn">BOOK NOW</span>
  </div>
  <div class="hero-copy">
    <h1>WELCOME TO<span>VELMIRA HEALTH</span></h1>
    <p>Lorem ipsum dolor sit amet, consectetur adipiscing elit.</p>
    <span class="btn">BOOK NOW</span>
  </div>
</header>

<section class="info">
  <div class="info-item">
    <div class="info-icon"><svg width="22" height="22" viewBox="0 0 24 24" fill="none" stroke="#5e9f3e" stroke-width="2.4"><circle cx="12" cy="12" r="9"/><path d="M12 7v5l3 2"/></svg></div>
    <h4>OPEN HOURS</h4><p>Mon – Fri 7am to 4:30pm<br>SUN CLOSED</p>
  </div>
  <div class="info-item">
    <div class="info-icon"><svg width="22" height="22" viewBox="0 0 24 24" fill="none" stroke="#5e9f3e" stroke-width="2.4"><rect x="3" y="6" width="18" height="12"/><path d="M3 6l9 7 9-7"/></svg></div>
    <h4>E-MAIL</h4><p>hello@velmirahealth.com</p>
  </div>
  <div class="info-item">
    <div class="info-icon"><svg width="22" height="22" viewBox="0 0 24 24" fill="#5e9f3e"><path d="M6.6 10.8a15 15 0 006.6 6.6l2.2-2.2c.3-.3.7-.4 1-.2 1.1.4 2.3.6 3.6.6.6 0 1 .4 1 1V20c0 .6-.4 1-1 1A17 17 0 013 4c0-.6.4-1 1-1h3.5c.6 0 1 .4 1 1 0 1.3.2 2.5.6 3.6.1.3 0 .7-.2 1z"/></svg></div>
    <h4>PHONE</h4><p>+1 555 014 2290</p>
  </div>
  <div class="info-item">
    <div class="info-icon"><svg width="22" height="22" viewBox="0 0 24 24" fill="#5e9f3e"><path d="M12 2a7 7 0 00-7 7c0 5 7 13 7 13s7-8 7-13a7 7 0 00-7-7zm0 9.5A2.5 2.5 0 1112 6.5a2.5 2.5 0 010 5z"/></svg></div>
    <h4>OUR LOCATION</h4><p>United States,<br>Velmira Health</p>
  </div>
</section>

<section class="services">
  <h2 class="section-title">OUR SERVICES</h2>
  <div class="cards">
    <article class="card">
      <div class="card-photo" role="img" aria-label="Hemodialysis machine display panel" style="background:linear-gradient(135deg,#3a5f86,#1f3552)"></div>
      <h3>HEMODIALYSIS</h3>
      <p>Lorem ipsum dolor sit amet, consectetur adipiscing elit, sed do eiusmod tempor incididunt ut labore</p>
      <span class="more">Learn More ›</span>
    </article>
    <article class="card">
      <div class="card-photo" role="img" aria-label="Clinicians performing peritoneal dialysis" style="background:linear-gradient(135deg,#6d8fb5,#2c476c)"></div>
      <h3>PERITONEAL DIALYSIS</h3>
      <p>Lorem ipsum dolor sit amet, consectetur adipiscing elit, sed do eiusmod tempor incididunt ut labore</p>
      <span class="more">Learn More ›</span>
    </article>
    <article class="card">
      <div class="card-photo" role="img" aria-label="Home hemodialysis equipment with tubing" style="background:linear-gradient(135deg,#b3475a,#3a5a8a)"></div>
      <h3>HOME HEMODIALYSIS.</h3>
      <p>Lorem ipsum dolor sit amet, consectetur adipiscing elit, sed do eiusmod tempor incididunt ut labore</p>
      <span class="more">Learn More ›</span>
    </article>
  </div>
</section>

<section class="about">
  <h2>ABOUT VELMIRA HEALTH</h2>
  <div class="tabs">
    <span class="tab">OUR MISSION</span><span class="tab active">OUR VISION</span><span class="tab">OUR TEAMS</span><span class="tab">FACILITY TOUR</span>
  </div>
  <div class="vision">
    <h3>OUR VISION</h3>
    <h4>Lorem ipsum dolor sit amet consectetur.</h4>
    <p>Lorem ipsum dolor sit amet, consectetur adipiscing elit, sed do eiusmod tempor incididunt ut labore et dolore magna aliqua. Ut enim ad minim veniam, quis nostrud exercitation ullamco laboris nisi ut aliquip ex ea commodo consequat.</p>
    <span class="btn">READ MORE</span>
  </div>
  <div class="vision-photo" role="img" aria-label="Glowing illustration of human kidneys"></div>
</section>

<section class="reviews">
  <h2 class="section-title">CLIENT REVIEWS</h2>
  <span class="arrow left"><svg width="12" height="12" viewBox="0 0 12 12" fill="none" stroke="#5e9f3e" stroke-width="2"><path d="M8 2L4 6l4 4"/></svg></span>
  <span class="arrow right"><svg width="12" height="12" viewBox="0 0 12 12" fill="none" stroke="#5e9f3e" stroke-width="2"><path d="M4 2l4 4-4 4"/></svg></span>
  <div class="review-row">
    <article class="review">
      <div class="review-head"><div class="avatar" role="img" aria-label="Reviewer portrait"></div><div><h4>Marcus Hale</h4><small>12 days ago</small><div class="stars">★★★★★</div></div></div>
      <p>Lorem ipsum dolor sit amet, consectetur adipiscing elit, sed do eiusmod tempor incididunt ut labore et dolore magna aliqua. Ut enim ad minim veniam, quis nostrud exercitation.</p>
    </article>
    <article class="review">
      <div class="review-head"><div class="avatar" role="img" aria-label="Reviewer portrait"></div><div><h4>Marcus Hale</h4><small>10 months ago</small><div class="stars">★★★★★</div></div></div>
      <p>Lorem ipsum dolor sit amet, consectetur adipiscing elit, sed do eiusmod tempor incididunt ut labore et dolore magna aliqua. Ut enim ad minim veniam, quis nostrud exercitation.</p>
    </article>
    <article class="review">
      <div class="review-head"><div class="avatar" role="img" aria-label="Reviewer portrait"></div><div><h4>Marcus Hale</h4><small>1 week ago</small><div class="stars">★★★★★</div></div></div>
      <p>Lorem ipsum dolor sit amet, consectetur adipiscing elit, sed do eiusmod tempor incididunt ut labore et dolore magna aliqua. Ut enim ad minim veniam, quis nostrud exercitation.</p>
    </article>
  </div>
</section>

<div class="map" role="img" aria-label="Street map showing the clinic location near the coast"></div>
<section class="contact">
  <h2>GET IN TOUCH</h2>
  <div class="form">
    <div class="field">First Name</div><div class="field">Last Name</div>
    <div class="field">E-mail</div><div class="field">Phone</div>
    <div class="field wide">Message</div>
  </div>
  <span class="submit">SUBMIT</span>
</section>

<footer class="footer">
  <div class="brand"><span class="brand-mark"></span>Velmira Health</div>
  <div class="cols">
    <div class="col"><h4>ABOUT INFO</h4><ul><li>Home</li><li>About</li><li>Services</li><li>Patient Information</li><li>Resources</li><li>Contact</li></ul></div>
    <div class="col"><h4>OUR SERVICES</h4><ul><li>Hemodialysis</li><li>Peritoneal Dialysis</li><li>Home Hemodialysis</li></ul>
      <h4 style="margin-top:20px">FOLLOW US</h4><div class="social"><span></span><span></span><span></span><span></span><span></span></div></div>
    <div class="col"><h4>QUICK LINKS</h4><ul><li>Terms of use</li><li>Privacy policy</li><li>Information</li><li>Cookies</li><li>FAQ</li><li>Site Map</li></ul></div>
    <div class="col" style="width:300px"><h4>CONTACT US</h4>
      <ul class="contact-list">
        <li><span class="mini"><svg width="14" height="14" viewBox="0 0 24 24" fill="#5e9f3e"><path d="M6.6 10.8a15 15 0 006.6 6.6l2.2-2.2c.3-.3.7-.4 1-.2 1.1.4 2.3.6 3.6.6.6 0 1 .4 1 1V20c0 .6-.4 1-1 1A17 17 0 013 4c0-.6.4-1 1-1h3.5c.6 0 1 .4 1 1 0 1.3.2 2.5.6 3.6.1.3 0 .7-.2 1z"/></svg></span>+1 555 014 2290</li>
        <li><span class="mini"><svg width="14" height="14" viewBox="0 0 24 24" fill="none" stroke="#5e9f3e" stroke-width="2.6"><rect x="3" y="6" width="18" height="12"/><path d="M3 6l9 7 9-7"/></svg></span>hello@velmirahealth.com</li>
        <li><span class="mini"><svg width="14" height="14" viewBox="0 0 24 24" fill="none" stroke="#5e9f3e" stroke-width="2.6"><circle cx="12" cy="12" r="9"/><path d="M12 7v5l3 2"/></svg></span>Mon – Fri 7am to 4:30pm; Sun Closed</li>
        <li><span class="mini"><svg width="14" height="14" viewBox="0 0 24 24" fill="#5e9f3e"><path d="M12 2a7 7 0 00-7 7c0 5 7 13 7 13s7-8 7-13a7 7 0 00-7-7zm0 9.5A2.5 2.5 0 1112 6.5a2.5 2.5 0 010 5z"/></svg></span>United States, Velmira Health</li>
      </ul>
    </div>
  </div>
  <div class="copy">© 2024 Velmira Health. All rights reserved.</div>
</footer>

</body>
</html>
```